Nitrogen generation business website

Project Overview:
This project aims to create a sleek, user-friendly, and responsive WordPress template for Flo7K3, a provider of Nitrogen generation solutions. The site will serve as a primary touchpoint for customers and businesses looking to enquire about or purchase Flo7K3 products and services. The website should clearly communicate the benefits of working with Flo7K3 as a distributor, focusing on ease of access, expert consultation, and fast, reliable service.
Target Audience:
• Industrial companies seeking Nitrogen solutions.
• Engineers, facility managers, and purchasing teams in need of high-quality Nitrogen systems.
• Partners or businesses seeking to collaborate or purchase through a distributor.
Key Objectives:
1. Establish Flo7K3’s Brand Identity: Use the bold, energetic logo and branding of Flo7K3 (as seen in the uploaded logo) throughout the design. Ensure the brand’s personality shines, with a focus on modernity, reliability, and innovation.
2. Showcase Products and Solutions: Display detailed product categories and descriptions, emphasising the solutions Flo7K3 offers.
3. Lead Generation: Incorporate contact forms, quote requests, and easy-to-find CTAs to convert visitors into leads.
4. User-Centric Design: The design must be intuitive and user-friendly, providing a smooth experience across desktop and mobile devices.
Design Requirements:
1. Home Page:
• Hero Banner: A dynamic, visually engaging hero banner featuring air and gas purification systems, paired with strong CTAs like “Request a Quote” or “Contact Us for Solutions.” The banner should align with the vibrant red and yellow tones in the Flo7K3 logo.
• Key Product Categories: Introduce the main product categories with icons or images linked to individual product pages.
• Flo7K3 Expertise Section: A section emphasising the company’s role as a trusted distributor, backed by experience and a strong partnership network.
• Why Choose Flo7K3: Highlight 3-4 major benefits, such as “Quick Delivery,” “Expert Consultation,” and “Innovative Technology.”
• Client Testimonials/Partners: Space for customer feedback, testimonials, or logos of partner companies to build trust.
• Newsletter or Enquiry Form: Place a compact form for capturing visitor details for quotes, enquiries, or subscriptions.
2. Product Pages:
• Category Pages: Create well-structured product category pages (e.g., Air Filtration Systems, Nitrogen Generators) similar to industry-standard designs. Each category page should feature professional imagery, short product descriptions, and links to detail pages.
• Product Detail Pages: Each product page will contain:
• High-quality images of the product.
• Detailed specifications, technical descriptions, and features.
• Options to download datasheets or brochures (PDF format).
• Clear CTAs to request a quote or contact sales.
• Product Comparison Tool (Optional): Allow users to compare multiple products, emphasising key features and specifications.
3. About Flo7K3 Page:
• Provide an overview of Flo7K3’s history, mission, and the value it provides as a leading distributor.
• Highlight industry expertise, the partnership network, and any accolades or certifications.
• Mention any regional advantages or special services (e.g., fast delivery times, on-site consultation).
4. Contact Us Page:
• Clean and Simple Form: Include fields for general inquiries or specific product requests.
• Contact Information: Display the company’s, email address info@flo7k3.co.uk.
5. Additional Functionalities:
• Responsive Design: Ensure the design is fully responsive, optimised for mobile, tablet, and desktop viewing.
• SEO Optimisation: Include best practices for search engine optimization (SEO), including clean URLs, meta tags, and image alt text.
• Fast Loading Speed: Optimise images, scripts, and code for fast loading times to improve user experience.
• Social Media Integration: Provide links to social media profiles (if applicable) and potentially include a feed for recent updates.
• Optional Blog: Create a blog space for sharing industry news, product updates, or educational content to engage with visitors and improve SEO.
Style Guide:
1. Color Palette:
• Use colors consistent with the Flo7K3 logo: Red (#FF0000) and Yellow (#FFD700) as primary colors. Incorporate neutral colors (such as white, gray, or black) for balance and readability.
• Accent colors may be introduced for subtle highlights, but the focus should be on the bold, energetic color scheme of Flo7K3.
2. Typography:
• Primary Font for Headings: A bold, modern sans-serif font that complements the strong branding of Flo7K3.
• Secondary Font for Body Text: Clean, easy-to-read sans-serif or serif font for optimal readability across devices.
• Typography Emphasis: Use large, bold typography for headlines to match the boldness of the logo and brand identity.
3. Imagery:
• Use high-quality industrial and technical imagery that reflects the air and gas purification products Flo7K3 distributes.
• Incorporate imagery showing products in action, e.g., in industrial settings or installations.
• Avoid clutter; ensure images are used to enhance user understanding, not overwhelm.
4. Icons:
• Utilise modern, flat-style icons that align with the clean and professional image of Flo7K3. Icons could represent services such as “Fast Delivery,” “Expert Support,” and “High-Quality Products.”
Functionality Requirements:
1. Content Management System (CMS): Build the site using WordPress for easy content management, allowing Flo7K3 staff to update content, product information, and blog posts.
2. Quote Request Integration: Ensure the site has a functional and easy-to-access “Request a Quote” form that appears on every product and service page.
3. Customer Support Section: Optionally include a section for FAQs, product guides, or a knowledge base to support customers and prospects.
4. Security: Implement SSL encryption and ensure that other security best practices (e.g., spam prevention for forms) are followed.
5. Multilingual Support (Optional): Provide the option to support multiple languages, depending on the regional scope of Flo7K3’s distribution services.
Deliverables:
• WordPress template with a homepage, product pages, about section, and contact page.
• SEO-friendly and responsive design.
• Clear CTAs for lead generation (e.g., “Request a Quote”).
• User-friendly interface for both desktop and mobile devices.
Inspiration/Competitors:
• Competitor Analysis: Research similar distributors in the air and gas purification industry for design inspiration.
• Brand Consistency: Ensure Flo7K3’s bold branding is prominent and differentiates it from competitors.
Target Market(s)
Food & Beverage manufacturers, Laser Cutting, Electronics manufacturers, General Industrial Manufacturers

```html
<!DOCTYPE html>
<html lang="en">
<head>
<meta charset="utf-8">
<title>Flo7K3 – Nitrogen Generation Solutions</title>
<link href="https://fonts.googleapis.com/css2?family=Montserrat:wght@500;600;700;800&family=Lato:wght@400;700&display=swap" rel="stylesheet">
<style>
:root{
  --red:#e8231a;
  --yellow:#f6b614;
  --gold:#e9a90e;
  --orange:#f57a10;
  --cream:#fff9ef;
  --grey:#f4f4f4;
  --ink:#1d1d1d;
  --muted:#555;
  --black:#0b0b0b;
  --btn:linear-gradient(180deg,var(--red) 0%,var(--orange) 60%,var(--yellow) 100%);
}
*{box-sizing:border-box;margin:0;padding:0}
html,body{width:1200px;height:4577px;overflow:hidden}
body{position:relative;background:#fff;font-family:'Lato',sans-serif;color:var(--ink)}
.abs{position:absolute}
.head-font{font-family:'Montserrat',sans-serif}
.btn{position:absolute;display:flex;align-items:center;justify-content:center;background:var(--btn);color:#1a0a00;font-family:'Montserrat',sans-serif;font-weight:700;font-size:15px;border-radius:24px 24px 24px 0;text-transform:uppercase;box-shadow:3px 4px 0 rgba(0,0,0,.08)}
.brand{font-family:'Montserrat',sans-serif;font-weight:800;color:var(--red);display:flex;align-items:center;gap:10px}
.brand i{display:block;width:14px;height:14px;border-radius:50%;background:var(--yellow)}
.section-title{position:absolute;left:0;width:1200px;text-align:center;font-family:'Montserrat',sans-serif;font-weight:800;font-size:42px;color:var(--red);text-transform:uppercase}
.section-title span{color:var(--yellow)}
.dots{position:absolute;left:582px;width:36px;height:18px}
.dots::before{content:"";position:absolute;left:0;top:4px;width:14px;height:14px;border-radius:50%;background:var(--yellow)}
.dots::after{content:"";position:absolute;left:24px;top:0;width:9px;height:9px;border-radius:50%;background:var(--red)}

/* top bar */
.topbar .contact{position:absolute;top:28px;font-size:16px;color:#222;display:flex;align-items:center;gap:8px}
.sep{position:absolute;top:26px;width:1px;height:24px;background:#333}
.nav{position:absolute;left:110px;top:80px;width:978px;height:62px;background:var(--red);border-radius:0 0 8px 8px;display:flex;align-items:center;z-index:2}
.nav a{position:absolute;color:#fff;font-family:'Montserrat',sans-serif;font-weight:600;font-size:14px;text-decoration:none;top:22px}
.nav a.active::after{content:"";position:absolute;left:0;right:0;bottom:-5px;height:2px;background:#fff}
.hero{position:absolute;left:0;top:114px;width:1200px;height:563px;background:linear-gradient(90deg,#2a2c2c 0%,#3d4243 45%,#5a6163 100%)}
.hero .kicker{position:absolute;left:112px;top:140px;color:#fff;font-family:'Montserrat',sans-serif;font-weight:700;font-size:25px}
.hero h1{position:absolute;left:110px;top:170px;color:#fff;font-family:'Montserrat',sans-serif;font-weight:800;font-size:96px;letter-spacing:-1px}
.hero p{position:absolute;left:112px;top:290px;width:360px;color:#fff;font-size:15px;line-height:27px}

/* about */
.about-text{position:absolute;left:180px;top:832px;width:840px;text-align:center;font-size:15px;line-height:30px;color:#333}

/* why */
.why{position:absolute;left:0;top:1139px;width:1200px;height:479px;background:var(--cream)}
.feature{position:absolute;width:240px;text-align:center}
.feature .ring{width:164px;height:164px;margin:0 auto;border-radius:50%;border:16px solid var(--yellow);background:#fff;display:flex;align-items:center;justify-content:center;box-shadow:0 0 0 4px #fbe2a8}
.feature h3{margin-top:22px;font-family:'Montserrat',sans-serif;font-weight:600;font-size:19px}

/* products */
.products{position:absolute;left:0;top:1618px;width:1200px;height:560px;background:linear-gradient(180deg,var(--gold),var(--yellow))}
.card{position:absolute;top:1795px;width:328px;height:432px;background:#fff;border:2px solid #ddd;border-radius:16px;text-align:center}
.card.active{border-color:var(--red);box-shadow:0 6px 14px rgba(0,0,0,.12)}
.card .img{margin:18px 16px 0;height:348px;border-radius:16px;background:linear-gradient(160deg,#e8e8e8,#cfcfcf)}
.card.active .img{height:290px;border:1px solid #999}
.card h3{margin-top:26px;font-family:'Montserrat',sans-serif;font-weight:700;font-size:19px}
.card.active h3{margin-top:24px}
.card p{margin-top:12px;padding:0 30px;font-size:13px;line-height:26px;color:#333}

/* testimonials */
.avatar{position:absolute;border-radius:50%;background:linear-gradient(160deg,#f1c9a3,#c88c63)}
.quote-text{position:absolute;left:280px;top:2802px;width:660px;text-align:center;font-family:'Montserrat',sans-serif;font-weight:500;font-size:15px;line-height:26px;color:#222}
.qmark{position:absolute;font-family:Georgia,serif;font-size:220px;color:#dcdcdc;line-height:1}

/* services */
.services{position:absolute;left:0;top:3022px;width:1200px;height:568px;background:var(--grey)}
.svc{position:absolute;top:3182px;width:299px;height:359px;border-radius:14px;overflow:hidden}
.svc .label{position:absolute;left:28px;right:28px;bottom:22px;display:flex;justify-content:space-between;align-items:center;color:#fff;font-family:'Montserrat',sans-serif;font-weight:700;font-size:17px}
.svc .label b{width:16px;height:16px;border-radius:50%;background:#fff;display:flex;align-items:center;justify-content:center}

/* contact */
.info{position:absolute;left:110px;display:flex;gap:22px}
.info .ico{width:62px;height:62px;border-radius:50%;background:var(--yellow);display:flex;align-items:center;justify-content:center}
.info h4{font-family:'Montserrat',sans-serif;font-weight:700;font-size:16px;margin-top:6px}
.info p{font-size:15px;margin-top:8px}
.field{position:absolute;background:#fff;box-shadow:0 2px 8px rgba(0,0,0,.13);font-size:14px;color:#666;padding:16px 18px}

/* footer */
.footer{position:absolute;left:0;top:4139px;width:1200px;height:438px;background:var(--black);color:#fff}
.footer h5{position:absolute;top:92px;font-family:'Montserrat',sans-serif;font-weight:600;font-size:20px}
.footer ul{position:absolute;top:130px;list-style:none;font-size:15px}
.footer li{height:35px}
.social{position:absolute;top:208px;width:26px;height:26px;border-radius:50%;border:2px solid #fff}
.social.on{background:var(--yellow);border-color:var(--yellow)}
</style>
</head>
<body>

<!-- Top bar -->
<header class="topbar">
  <div class="brand abs" style="left:112px;top:20px;font-size:40px">Flo7K3<i></i></div>
  <div class="contact" style="left:370px">
    <svg width="14" height="14" viewBox="0 0 24 24"><path fill="#333" d="M6.6 10.8a15 15 0 0 0 6.6 6.6l2.2-2.2c.3-.3.7-.4 1-.2 1.1.4 2.3.6 3.6.6.6 0 1 .4 1 1V20c0 .6-.4 1-1 1A17 17 0 0 1 3 4c0-.6.4-1 1-1h3.5c.6 0 1 .4 1 1 0 1.3.2 2.5.6 3.6.1.3 0 .7-.2 1z"/></svg>
    +1 555 204 7391
  </div>
  <span class="sep" style="left:558px"></span>
  <div class="contact" style="left:592px">
    <svg width="14" height="12" viewBox="0 0 24 20"><path fill="#333" d="M2 0h20a2 2 0 0 1 2 2v16a2 2 0 0 1-2 2H2a2 2 0 0 1-2-2V2a2 2 0 0 1 2-2zm10 9 10-6H2z"/></svg>
    info@flo7k3.co.uk
  </div>
  <span class="sep" style="left:792px"></span>
  <div class="btn" style="left:838px;top:20px;width:250px;height:38px;font-size:13px;color:#fff;border-radius:20px 20px 20px 0">Contact us for solutions</div>
</header>

<nav class="nav">
  <a class="active" style="left:40px">HOME</a>
  <a style="left:166px">ABOUT</a>
  <a style="left:299px">PRODUCT</a>
  <a style="left:448px">SERVICES</a>
  <a style="left:600px">INDUSTRIES</a>
  <a style="left:770px">CONTACT US</a>
  <span class="abs" style="left:928px;top:19px;width:24px;height:24px;border-radius:50%;background:#fff;display:flex;align-items:center;justify-content:center">
    <svg width="11" height="11" viewBox="0 0 24 24"><circle cx="10" cy="10" r="7" fill="none" stroke="#333" stroke-width="3"/><path d="M15 15l6 6" stroke="#333" stroke-width="3"/></svg>
  </span>
</nav>

<!-- Hero -->
<section class="hero" role="img" aria-label="Industrial plant backdrop with nitrogen generator, filter housing and filter cartridges">
  <div class="kicker">WELCOME TO</div>
  <h1>FLO7K3</h1>
  <p>Lorem ipsum dolor sit amet, consectetur adipiscing elit, sed do eiusmod tempor incididunt ut labore et dolore magna aliqua.</p>
  <div class="btn" style="left:112px;top:392px;width:200px;height:48px;background:var(--yellow)">Request a quote</div>
  <div class="abs" role="img" aria-label="Filter housing and cartridges" style="left:568px;top:130px;width:260px;height:360px;border-radius:16px;background:linear-gradient(180deg,#8b9296,#c6cacc);opacity:.85"></div>
  <div class="abs" role="img" aria-label="Compact nitrogen generator unit" style="left:838px;top:60px;width:290px;height:470px;border-radius:18px;background:linear-gradient(160deg,#e6e6e6,#a9acae)"></div>
</section>

<!-- About -->
<span class="dots" style="top:738px"></span>
<h2 class="section-title" style="top:760px">About <span>Flo7K3</span></h2>
<div class="about-text">
  Flo7K3 specialises in supplying, installing, and servicing nitrogen generators for efficient on-site nitrogen production. Enhance your operations with our reliable, cost-effective nitrogen solutions. Discover how our advanced nitrogen generators can optimise your business today.
</div>
<div class="about-text" style="top:952px">Contact Flo7K3 for expert nitrogen generation services.</div>
<div class="btn" style="left:498px;top:1013px;width:168px;height:50px">Get started</div>

<!-- Why choose us -->
<section class="why">
  <span class="dots" style="top:76px"></span>
  <h2 class="section-title" style="top:98px">Why <span>choose us</span></h2>
  <div class="feature" style="left:138px;top:183px">
    <div class="ring"><svg width="66" height="60" viewBox="0 0 66 60" fill="none" stroke="var(--red)" stroke-width="2.5"><rect x="4" y="18" width="34" height="26" rx="2"/><path d="M38 26h12l8 10v8H38z"/><circle cx="14" cy="48" r="5"/><circle cx="48" cy="48" r="5"/><circle cx="26" cy="10" r="8" stroke="var(--orange)"/><path d="M26 6v4h3" stroke="var(--orange)"/></svg></div>
    <h3>Quick Delivery</h3>
  </div>
  <div class="feature" style="left:467px;top:183px">
    <div class="ring"><svg width="66" height="60" viewBox="0 0 66 60" fill="none" stroke="var(--red)" stroke-width="2.5"><circle cx="33" cy="14" r="9" stroke="var(--orange)"/><path d="M30 24h6"/><circle cx="14" cy="34" r="5"/><circle cx="52" cy="34" r="5"/><path d="M4 56c0-9 4-14 10-14s10 5 10 14M42 56c0-9 4-14 10-14s10 5 10 14M22 46h22"/></svg></div>
    <h3>Expert Consultation</h3>
  </div>
  <div class="feature" style="left:795px;top:183px">
    <div class="ring"><svg width="64" height="64" viewBox="0 0 64 64" fill="none" stroke="var(--red)" stroke-width="2.5"><circle cx="32" cy="32" r="16"/><circle cx="32" cy="32" r="6" stroke="var(--orange)"/><path d="M32 6v8M32 50v8M6 32h8M50 32h8M14 14l6 6M44 44l6 6M50 14l-6 6M14 50l6-6"/></svg></div>
    <h3>Innovative Technology</h3>
  </div>
</section>

<!-- Product categories -->
<section class="products">
  <span class="dots" style="top:72px"></span>
  <h2 class="section-title" style="top:92px;color:#fff">Our product categories</h2>
  <svg class="abs" style="left:0;top:300px" width="1200" height="260" viewBox="0 0 1200 260" preserveAspectRatio="none"><path d="M0 120 Q600 -60 1200 120 V260 H0 Z" fill="#fff"/></svg>
</section>
<div class="card" style="left:71px">
  <div class="img" role="img" aria-label="Air filter housings and filter cartridges"></div>
  <h3>AIR FILTERATION</h3>
</div>
<div class="card active" style="left:437px">
  <div class="img" role="img" aria-label="Industrial nitrogen generator skid"></div>
  <h3>NITROGEN GENERATOR</h3>
  <p>Excepteur sint occaecat cupidatat non proident, sunt in culpa</p>
</div>
<div class="card" style="left:802px">
  <div class="img" role="img" aria-label="Pre-treatment dryer units"></div>
  <h3>PRE-TREATMENT</h3>
</div>
<div class="btn" style="left:516px;top:2302px;width:168px;height:50px">View more</div>

<!-- Testimonials -->
<span class="dots" style="top:2426px"></span>
<h2 class="section-title" style="top:2448px">What our <span>customer says</span></h2>
<div class="avatar" role="img" aria-label="Customer portrait" style="left:542px;top:2541px;width:136px;height:136px"></div>
<div class="avatar" role="img" aria-label="Customer portrait" style="left:137px;top:2615px;width:66px;height:66px"></div>
<div class="avatar" role="img" aria-label="Customer portrait" style="left:1015px;top:2543px;width:46px;height:46px"></div>
<span class="abs" style="left:382px;top:2654px;width:13px;height:13px;border-radius:50%;background:var(--red)"></span>
<span class="abs" style="left:898px;top:2617px;width:6px;height:6px;border-radius:50%;background:var(--yellow)"></span>
<div class="abs head-font" style="left:0;width:1220px;text-align:center;top:2698px;font-weight:600;font-size:20px">Marcus Hellwin</div>
<div class="abs" style="left:0;width:1220px;text-align:center;top:2731px;font-size:12px;color:#777">United States</div>
<div class="abs" style="left:0;width:1220px;text-align:center;top:2752px;font-size:30px;color:var(--yellow);letter-spacing:1px">★★★★★</div>
<div class="qmark" style="left:166px;top:2700px">&ldquo;</div>
<div class="qmark" style="left:955px;top:2790px">&rdquo;</div>
<div class="quote-text">Itaque earum rerum hic tenetur a sapiente delectus, ut aut reiciendis voluptatibus maiores alias. Consequatur aut perferendis doloribus asperiores repellat.Et harum quidem rerum facilis est et expedita distinctio.</div>
<div class="abs" style="left:540px;top:2912px;display:flex;gap:8px">
  <i style="width:14px;height:14px;border-radius:50%;background:#d9dcec"></i><i style="width:14px;height:14px;border-radius:50%;background:#d9dcec"></i><i style="width:14px;height:14px;border-radius:50%;background:#d9dcec"></i><i style="width:14px;height:14px;border-radius:50%;background:var(--yellow)"></i><i style="width:14px;height:14px;border-radius:50%;background:#d9dcec"></i><i style="width:14px;height:14px;border-radius:50%;background:#d9dcec"></i>
</div>

<!-- Services -->
<section class="services">
  <span class="dots" style="top:60px"></span>
  <h2 class="section-title" style="top:82px">Our <span>services</span></h2>
</section>
<div class="svc" role="img" aria-label="Engineers consulting in a plant" style="left:112px;background:linear-gradient(180deg,#7fa2c4,#2e4a66 70%,#132232)">
  <div class="label">CONSULTATION<b><svg width="8" height="8" viewBox="0 0 8 8"><path d="M2 1l3 3-3 3" stroke="#222" stroke-width="1.6" fill="none"/></svg></b></div>
</div>
<div class="svc" role="img" aria-label="Refinery installation at dusk" style="left:450px;background:linear-gradient(180deg,#a7a9cf,#d9a98d 45%,#3c2f2d 80%,#161313)">
  <div class="label">INSTALLATION<b><svg width="8" height="8" viewBox="0 0 8 8"><path d="M2 1l3 3-3 3" stroke="#222" stroke-width="1.6" fill="none"/></svg></b></div>
</div>
<div class="svc" role="img" aria-label="Technician performing maintenance" style="left:788px;background:linear-gradient(180deg,#6e6f6c,#a78c5f 50%,#2a2620)">
  <div class="label">MAINTENANCE<b><svg width="8" height="8" viewBox="0 0 8 8"><path d="M2 1l3 3-3 3" stroke="#222" stroke-width="1.6" fill="none"/></svg></b></div>
</div>

<!-- Contact -->
<span class="dots" style="top:3630px"></span>
<h2 class="section-title" style="top:3652px">Get in <span>touch with us</span></h2>
<div class="info" style="top:3750px">
  <div class="ico"><svg width="20" height="26" viewBox="0 0 20 26"><path fill="#fff" d="M10 0a10 10 0 0 0-10 10c0 7 10 16 10 16s10-9 10-16A10 10 0 0 0 10 0zm0 14a4 4 0 1 1 0-8 4 4 0 0 1 0 8z"/></svg></div>
  <div><h4>LOCATION</h4><p>Flo7K3, United States</p></div>
</div>
<div class="info" style="top:3876px">
  <div class="ico"><svg width="22" height="22" viewBox="0 0 24 24"><path fill="#fff" d="M6.6 10.8a15 15 0 0 0 6.6 6.6l2.2-2.2c.3-.3.7-.4 1-.2 1.1.4 2.3.6 3.6.6.6 0 1 .4 1 1V20c0 .6-.4 1-1 1A17 17 0 0 1 3 4c0-.6.4-1 1-1h3.5c.6 0 1 .4 1 1 0 1.3.2 2.5.6 3.6.1.3 0 .7-.2 1z"/></svg></div>
  <div><h4>PHONE NUMBER</h4><p>+1 555 204 7391</p></div>
</div>
<div class="info" style="top:3990px">
  <div class="ico"><svg width="22" height="18" viewBox="0 0 24 20"><path fill="#fff" d="M2 0h20a2 2 0 0 1 2 2v16a2 2 0 0 1-2 2H2a2 2 0 0 1-2-2V2a2 2 0 0 1 2-2zm10 9 10-6H2z"/></svg></div>
  <div><h4>EMAIL ADDRESS</h4><p>info@flo7k3.co.uk</p></div>
</div>
<div class="field" style="left:507px;top:3737px;width:283px;height:48px">First Name</div>
<div class="field" style="left:801px;top:3737px;width:283px;height:48px">Your Email</div>
<div class="field" style="left:507px;top:3799px;width:283px;height:48px">Your Phone</div>
<div class="field" style="left:801px;top:3799px;width:283px;height:48px;display:flex;justify-content:space-between">Service<svg width="10" height="8" viewBox="0 0 10 8" style="margin-top:4px"><path d="M0 0h10L5 7z" fill="#333"/></svg></div>
<div class="field" style="left:507px;top:3866px;width:577px;height:103px">Message</div>
<div class="btn" style="left:507px;top:4005px;width:168px;height:50px">Submit</div>

<!-- Footer -->
<footer class="footer">
  <div class="brand abs" style="left:112px;top:98px;font-size:48px">Flo7K3<i></i></div>
  <span class="social on" style="left:111px"></span>
  <span class="social" style="left:158px"></span>
  <span class="social" style="left:202px"></span>
  <span class="social" style="left:248px"></span>

  <h5 style="left:386px">QUICK LINKS</h5>
  <ul style="left:392px"><li>Home</li><li>Products</li><li>Services</li><li>Blog</li><li>Contact Us</li></ul>

  <h5 style="left:592px">HELP LINKS</h5>
  <ul style="left:595px"><li>FAQ</li><li>Terms of use</li><li>Privacy Policy</li><li>Support Links</li><li>Conditions</li></ul>

  <h5 style="left:793px;top:81px">NEWSLETTER</h5>
  <div class="abs" style="left:793px;top:122px;width:293px;height:45px;background:#fff;border-radius:6px;color:#888;font-size:13px;padding:14px 18px">Enter The Email</div>
  <div class="btn" style="left:791px;top:193px;width:169px;height:50px">Subscribe us</div>

  <div class="abs" style="left:110px;top:346px;width:978px;height:1px;background:#777"></div>
  <div class="abs head-font" style="left:0;width:1200px;top:384px;text-align:center;font-weight:600;font-size:15px">Copyrights@2024.Flo7K3.All Rights Reserved</div>
</footer>

</body>
</html>
```